I have been working as Brivo Local Accountant and am wanting to rebrand. I have already set up a website and had some post cards done for Corvanta 8 using poldra press. I want to stick with this logo and style but want to use the same setup as the Brivo stationary attached. Can I please have a proof of an Envelope, Business Card, Letterhead and With Compliments Slip. I need these as soon as possible.

Please not the following address details;

CORVANTA 8 (The trading name)
Accountant & Tax Agent (Just a bit about what we do)
Office 5/42-44 Harlow Street
Kestrel Point NSW 2619

P: 07 5512 8403 F: 07 5512 6403
E: Info@Corvanta8.example.com.au
W: www.corvanta8.example.com.au

It also does not have to be just one puzzle piece and it does not have to be block colour if that helps - I just like the concept of the puzzle piece as I feel like I am apart of peoples businesses if you know what I mean.

Sorry the address is Office 5, 42-44 Harlow Street, Tweed Heads  NSW  2485

Can you please use updated address in thebreif, include PO Box 639 and use my mobile on business card only.  My ABN Is 42 608315927.  Also can you only use the RFQ and Brivo logon at the bottom on the letter head and with comp slips.

I am trying to upload the Brivo Logo now.

Thanks
Delia

Reason: I just want some more time to cover some changes and colour etc. This is hard from my end - I am accountant without a creative bone. Thanks for your patience. Delia

Target Market(s)

My business is a business of trust

Font styles to use
Sans Serif

Colors
9bcb3c

Requirements
Should not have
• Please tak off the Quality GLX 4410 & cover of excellence logos

```html
<!DOCTYPE html>
<html lang="en">
<head>
<meta charset="utf-8">
<title>Corvanta 8 Stationery Proof</title>
<link rel="stylesheet" href="https://fonts.googleapis.com/css2?family=Arimo:wght@400;700&family=Open+Sans:ital,wght@1,400;1,600&display=swap">
<style>
  :root {
    --brand-green: #9bcb3c;
    --edge-black: #222222;
    --ink: #1a1a1a;
    --paper: #ffffff;
    --stage: #ffffff;
    --badge-grey: #c9ccd1;
  }
  * { box-sizing: border-box; margin: 0; padding: 0; }
  html, body { width: 1200px; height: 819px; overflow: hidden; background: var(--stage); }
  body { position: relative; font-family: "Arimo", Arial, sans-serif; color: var(--ink); }

  .sheet {
    position: absolute;
    background: var(--paper);
    box-shadow: 3px 4px 8px rgba(0,0,0,0.35);
    overflow: hidden;
  }
  .sheet-edge { position: absolute; left: 0; top: 0; bottom: 0; width: 10px; background: var(--edge-black); }

  .brand { position: absolute; }
  .brand-mark { position: absolute; left: 0; top: 0; background: var(--brand-green); }
  .brand-name { position: absolute; white-space: nowrap; font-weight: 400; color: var(--ink); line-height: 1; }
  .brand-tagline { position: absolute; white-space: nowrap; text-transform: uppercase; line-height: 1; letter-spacing: 0.02em; }

  .small-text { position: absolute; white-space: nowrap; }

  .web-italic { font-family: "Open Sans", Arial, sans-serif; font-style: italic; color: var(--brand-green); white-space: nowrap; }

  .rule { position: absolute; height: 2px; background: var(--brand-green); }

  .member-badge { position: absolute; background: var(--badge-grey); }

  .partner-name { position: absolute; color: var(--ink); font-weight: 400; line-height: 1; white-space: nowrap; }

  /* With compliments slip */
  .comp-slip { left: 51px; top: 26px; width: 503px; height: 230px; }
  .comp-slip .vertical-web {
    position: absolute; left: 20px; top: 16px; height: 196px;
    writing-mode: vertical-rl; transform: rotate(180deg);
    font-size: 12px; text-align: left;
  }
  .comp-slip .greeting { position: absolute; left: 190px; top: 27px; font-size: 12px; }
  .comp-slip .brand { left: 300px; top: 5px; }
  .comp-slip .brand-mark { width: 46px; height: 46px; }
  .comp-slip .brand-name { left: 50px; top: 7px; font-size: 25px; }
  .comp-slip .brand-tagline { left: 51px; top: 35px; font-size: 7.5px; }
  .comp-slip .rule { left: 66px; top: 182px; width: 413px; }
  .comp-slip .address { left: 72px; top: 189px; font-size: 7px; line-height: 9px; }
  .comp-slip .member-badge { left: 247px; top: 189px; width: 40px; height: 23px; }
  .comp-slip .partner-name { left: 340px; top: 194px; font-size: 13px; }

  /* Business card */
  .business-card { left: 145px; top: 288px; width: 337px; height: 195px; }
  .business-card .brand { left: 26px; top: 14px; }
  .business-card .brand-mark { width: 40px; height: 40px; }
  .business-card .brand-name { left: 44px; top: 4px; font-size: 22px; }
  .business-card .brand-tagline { left: 45px; top: 29px; font-size: 6.5px; }
  .business-card .contact { position: absolute; right: 10px; top: 62px; text-align: right; font-size: 8px; line-height: 10px; }
  .business-card .contact-name { font-size: 11px; font-weight: 700; line-height: 13px; }
  .business-card .contact-role { color: var(--brand-green); }
  .business-card .address { left: 26px; top: 126px; font-size: 7.5px; line-height: 9.5px; }
  .business-card .rule { left: 10px; top: 163px; width: 327px; }
  .business-card .card-web { position: absolute; right: 8px; top: 168px; font-size: 14px; }

  /* Envelope */
  .envelope { left: 32px; top: 506px; width: 565px; height: 285px; }
  .envelope .brand { left: 27px; top: 27px; }
  .envelope .brand-mark { width: 40px; height: 40px; }
  .envelope .brand-name { left: 44px; top: 4px; font-size: 22px; }
  .envelope .brand-tagline { left: 45px; top: 29px; font-size: 6.5px; }
  .envelope .address { left: 27px; top: 229px; font-size: 7.5px; line-height: 10px; }

  /* Letterhead */
  .letterhead { left: 613px; top: 23px; width: 541px; height: 768px; }
  .letterhead .sheet-edge { width: 14px; }
  .letterhead .brand { left: 305px; top: 24px; }
  .letterhead .brand-mark { width: 55px; height: 55px; }
  .letterhead .brand-name { left: 60px; top: 6px; font-size: 31px; }
  .letterhead .brand-tagline { left: 61px; top: 39px; font-size: 9.5px; }
  .letterhead .footer-line { left: 37px; top: 686px; font-size: 7px; font-weight: 700; letter-spacing: -0.01em; }
  .letterhead .rule { left: 37px; top: 697px; width: 473px; }
  .letterhead .registration { left: 63px; top: 705px; font-size: 7.5px; line-height: 10px; display: grid; grid-template-columns: 46px auto; }
  .letterhead .member-badge { left: 218px; top: 704px; width: 60px; height: 35px; }
  .letterhead .partner-name { left: 330px; top: 712px; font-size: 19px; }
</style>
</head>
<body>

<section class="sheet comp-slip" aria-label="With compliments slip">
  <div class="sheet-edge"></div>
  <div class="vertical-web web-italic">www.corvanta8.example.com.au</div>
  <div class="greeting web-italic">with compliments</div>
  <div class="brand">
    <div class="brand-mark"></div>
    <div class="brand-name">Corvanta 8</div>
    <div class="brand-tagline">Accountant &amp; Tax Agent</div>
  </div>
  <div class="rule"></div>
  <div class="small-text address">Office 5, 42-44 Harlow Street,<br>PO Box 639, Kestrel Point&nbsp; NSW&nbsp; 2619<br>P: 07 5512 8403 | F: 07 5512 6403</div>
  <div class="member-badge" role="img" aria-label="RFQ member badge"></div>
  <div class="partner-name">Brivo Local Accountant</div>
</section>

<section class="sheet business-card" aria-label="Business card">
  <div class="sheet-edge"></div>
  <div class="brand">
    <div class="brand-mark"></div>
    <div class="brand-name">Corvanta 8</div>
    <div class="brand-tagline">Accountant &amp; Tax Agent</div>
  </div>
  <div class="contact">
    <div class="contact-name">Delia Hartwell</div>
    <div class="contact-role">Director</div>
    <div>M: 0455 318 206</div>
    <div>E: delia.hartwell@corvanta8.example.com.au</div>
  </div>
  <div class="small-text address">A: Office 5, 42-44 Harlow Street,<br>PO Box 639, Kestrel Point&nbsp; NSW&nbsp; 2619<br>P: 07 5512 8403 | F: 07 5512 6403</div>
  <div class="rule"></div>
  <div class="card-web web-italic">www.corvanta8.example.com.au</div>
</section>

<section class="sheet envelope" aria-label="Envelope">
  <div class="sheet-edge"></div>
  <div class="brand">
    <div class="brand-mark"></div>
    <div class="brand-name">Corvanta 8</div>
    <div class="brand-tagline">Accountant &amp; Tax Agent</div>
  </div>
  <div class="small-text address">Office 5, 42-44 Harlow Street,<br>PO Box 639 Kestrel Point NSW 2619<br>www.corvanta8.example.com.au</div>
</section>

<section class="sheet letterhead" aria-label="Letterhead">
  <div class="sheet-edge"></div>
  <div class="brand">
    <div class="brand-mark"></div>
    <div class="brand-name">Corvanta 8</div>
    <div class="brand-tagline">Accountant &amp; Tax Agent</div>
  </div>
  <div class="small-text footer-line">P: 07 5512 8403 | F: 07 5512 6403 | Office 5, 42-44 Harlow St., PO Box 639, Kestrel Point, NSW&nbsp; 2619 | www.corvanta8.example.com.au</div>
  <div class="rule"></div>
  <div class="small-text registration">
    <span>Director :</span><span>42 608315927</span>
    <span></span><span>Delia Hartwell</span>
  </div>
  <div class="member-badge" role="img" aria-label="RFQ member badge"></div>
  <div class="partner-name">Brivo Local Accountant</div>
</section>

</body>
</html>
```